I need a business card design for my vidloomer channel called The Tidy Skillet Show. I make vidloomer cooking tutorials. I'd like the phrase " I'll see you next time, for my next meal" somewhere on the BC. The Vidloomer web address is www.vidloomer.example/user/TidySkilletShow
email - bookings@harrowlanemedia.example

Target Market(s)

This is for companies & business opportunities so it needs to look professional & sleek.

Industry/Entity Type

Cooking

Requirements
Must have
• Must have my Tidy skillet show logo on the card preferably top left. My name ( Marcus Delroy ). Name of my channel "Tidy Skillet Show" & the vidlomer logo & web address for my channel & the email bookings@harrowlanemedia.example & the 3 pics of food.

```html
<!DOCTYPE html>
<html lang="en">
<head>
<meta charset="utf-8">
<title>The Tidy Skillet Show – Business Card</title>
<link rel="stylesheet" href="https://fonts.googleapis.com/css2?family=Kaushan+Script&family=Josefin+Sans:wght@400;600&family=Questrial&display=swap">
<style>
  :root {
    --page-bg: #e9e5df;
    --header-black: #0b0b0b;
    --brand-orange: #f7941d;
    --footer-orange: #f6a01f;
    --ink-dark: #2b2119;
    --ink-white: #ffffff;
    --wood-light: #b58a5c;
    --wood-mid: #9a7048;
    --wood-dark: #7a5434;
    --channel-red: #d3242b;
    --mail-blue: #25479b;
  }
  * { margin: 0; padding: 0; box-sizing: border-box; }
  html, body {
    width: 1200px;
    height: 1000px;
    overflow: hidden;
    background: var(--page-bg);
  }
  .card {
    position: absolute;
    left: 340px;
    top: 45px;
    width: 520px;
    height: 910px;
    background: var(--wood-mid);
    box-shadow: 0 6px 18px rgba(0,0,0,0.18);
    overflow: hidden;
  }

  /* Header band */
  .card-header {
    position: absolute;
    left: 0; top: 0;
    width: 100%; height: 267px;
    background: var(--header-black);
  }
  .host-emblem {
    position: absolute;
    left: 28px; top: 14px;
    width: 210px; height: 238px;
  }
  .host-emblem-art {
    position: absolute;
    left: 0; top: 0;
    width: 210px; height: 178px;
    background: radial-gradient(circle at 50% 45%, #f2efe9 0%, #d9a35c 35%, #c2741c 60%, #0b0b0b 82%);
  }
  .emblem-name {
    position: absolute;
    left: 18px; top: 190px;
    display: flex;
    align-items: center;
    gap: 10px;
  }
  .emblem-mark {
    width: 28px; height: 28px;
    background: var(--brand-orange);
  }
  .emblem-text {
    font-family: "Josefin Sans", sans-serif;
    font-weight: 600;
    font-size: 17px;
    line-height: 1.05;
    color: var(--ink-white);
    text-transform: uppercase;
  }
  .channel-title {
    position: absolute;
    left: 258px; top: 26px;
    width: 250px;
    text-align: center;
  }
  .channel-title-script {
    font-family: "Kaushan Script", cursive;
    font-size: 62px;
    line-height: 0.98;
    color: var(--brand-orange);
  }
  .channel-title-sub {
    font-family: "Josefin Sans", sans-serif;
    font-weight: 600;
    font-size: 34px;
    letter-spacing: 1px;
    color: var(--ink-white);
    margin-top: 4px;
  }

  /* Wood panel */
  .wood-panel {
    position: absolute;
    left: 0; top: 267px;
    width: 100%; height: 555px;
    background: linear-gradient(180deg, var(--wood-light) 0%, var(--wood-mid) 45%, var(--wood-dark) 100%);
  }
  .host-name {
    position: absolute;
    left: 0; top: 300px;
    width: 100%;
    text-align: center;
    font-family: "Kaushan Script", cursive;
    font-size: 60px;
    color: var(--brand-orange);
    -webkit-text-stroke: 10px var(--ink-white);
    paint-order: stroke fill;
  }
  .contact-list {
    position: absolute;
    left: 58px; top: 405px;
    list-style: none;
  }
  .contact-item {
    display: flex;
    align-items: center;
    gap: 26px;
    font-family: "Questrial", sans-serif;
    font-size: 21px;
    line-height: 1.2;
    color: var(--ink-dark);
  }
  .contact-item + .contact-item { margin-top: 26px; }
  .channel-icon {
    width: 40px; height: 40px;
    background: var(--channel-red);
    flex: none;
  }
  .mail-icon { width: 56px; height: 38px; flex: none; }
  .contact-item.mail { gap: 22px; margin-left: -8px; }

  /* Food photos */
  .food-photos {
    position: absolute;
    left: 0; top: 530px;
    width: 100%; height: 292px;
    background:
      radial-gradient(ellipse at 85% 45%, #4a2a1a 0%, #6a3a22 25%, transparent 48%),
      radial-gradient(ellipse at 58% 80%, #c8281e 0%, #e0651a 20%, transparent 40%),
      radial-gradient(ellipse at 22% 50%, #2d7fb5 0%, #4aa0c8 12%, transparent 30%),
      linear-gradient(90deg, #e8df8a 0%, #d9cf6e 40%, #a24a2e 70%, #5a331f 100%);
  }

  /* Footer band */
  .card-footer {
    position: absolute;
    left: 0; top: 822px;
    width: 100%; height: 88px;
    background: var(--footer-orange);
    display: flex;
    align-items: center;
    justify-content: center;
    text-align: center;
  }
  .signoff {
    font-family: "Josefin Sans", sans-serif;
    font-weight: 600;
    font-size: 24px;
    line-height: 1.15;
    letter-spacing: 1px;
    color: var(--ink-dark);
    text-transform: uppercase;
    padding-top: 4px;
  }
</style>
</head>
<body>
  <article class="card">
    <header class="card-header">
      <div class="host-emblem">
        <div class="host-emblem-art" role="img" aria-label="Illustrated chef host holding cooking utensils"></div>
        <div class="emblem-name">
          <span class="emblem-mark"></span>
          <span class="emblem-text">Tidy Skillet<br>Show</span>
        </div>
      </div>
      <div class="channel-title">
        <div class="channel-title-script">Tidy<br>Skillet</div>
        <div class="channel-title-sub">SHOW</div>
      </div>
    </header>

    <section class="wood-panel" role="img" aria-label="Wooden plank background"></section>

    <h1 class="host-name">Marcus Delroy</h1>

    <ul class="contact-list">
      <li class="contact-item channel">
        <span class="channel-icon"></span>
        <span>www.vidloomer.example/user/<br>TidySkilletShow</span>
      </li>
      <li class="contact-item mail">
        <svg class="mail-icon" viewBox="0 0 56 38" aria-hidden="true">
          <rect x="1" y="1" width="54" height="36" rx="3" fill="var(--mail-blue)"/>
          <polyline points="3,4 28,22 53,4" fill="none" stroke="#ffffff" stroke-width="2.5"/>
        </svg>
        <span>bookings@harrowlanemedia.example</span>
      </li>
    </ul>

    <div class="food-photos" role="img" aria-label="Three food photos: a pool party cake, a rainbow jelly slice and a candy-filled chocolate cake"></div>

    <footer class="card-footer">
      <p class="signoff">I'll see you next time,<br>for my next meal</p>
    </footer>
  </article>
</body>
</html>
```